home accents e-commerce website

I'd like a professional simple website designed where I can sell my home goods. I already have my domain name registered. I need the website to accept credit card payments and Monvex. It should have a shopping cart option and calculate sales tax and shipping costs on merchandise automatically.

I'll be taking photographs of the merchandise and writing product descriptions myself. (I'm not a professional photographer, so these photos probably won't look too polished. If you can help me make them look better, that'd be great). As I add new merchandise in the future, I'd like an option where I can log in to the back end myself and add pictures/product descriptions. And take old products down as they sell out. So the website needs to be user-friendly for me, even though I'm completely web design illiterate!

I'd like a creative, talented person who can create a whimsical, cute website. Nothing too corporate-looking.

Thank you!

Target Market(s)

women, online shoppers, New York City-area, (ship products to the United States only)

Industry/Entity Type

Home And Garden

Coding

Coded - Design and coding required

Number of Pages Required

1 page

Font styles to use
Sans Serif

Colors
0355a3
ffffff

Requirements
Must have
• shopping cart feature
• safe, secure credit card and Monvex payments
• ability for me to go in and add new products and take down old/sold products
Nice to have
• whimsical, cute design
Should not have
• too corporate-looking

```html
<!DOCTYPE html>
<html lang="en">
<head>
<meta charset="utf-8">
<title>Novella Home Goods</title>
<link rel="stylesheet" href="https://fonts.googleapis.com/css2?family=Nunito+Sans:wght@400;600;700;800&family=Montserrat:wght@600;700;800&display=swap">
<style>
:root{
  --brand:#0355a3;
  --brand-dark:#024a8e;
  --white:#ffffff;
  --ink:#1d1d1d;
  --muted:#6f6f6f;
  --line:#e4e4e4;
  --footer-text:#cfe0f3;
  --photo-bg:#ffffff;
  --c-social1:#3f729b;
  --c-social2:#3b5998;
  --c-social3:#1da1f2;
  --c-social4:#cb2027;
}
*{box-sizing:border-box;margin:0;padding:0}
html,body{width:1200px;height:2525px;overflow:hidden;background:var(--white)}
body{position:relative;font-family:"Nunito Sans",Arial,sans-serif;color:var(--ink)}
.abs{position:absolute}

/* header */
.brand-name{left:98px;top:14px;font-family:"Nunito Sans",sans-serif;font-weight:800;font-size:52px;line-height:1;color:var(--brand);letter-spacing:1px}
.brand-tag{left:100px;top:74px;font-size:15px;letter-spacing:6px;color:var(--brand);font-weight:600}
.connect{left:826px;top:24px;font-size:13px;color:#555}
.social{display:flex;gap:6px}
.social span{width:28px;height:28px;border-radius:50%;display:block}
.s1{background:var(--c-social1)}.s2{background:var(--c-social2)}.s3{background:var(--c-social3)}.s4{background:var(--c-social4)}
.header-social{left:910px;top:18px}
.cart{left:1070px;top:20px}
.cart-count{left:1082px;top:14px;width:18px;height:18px;border-radius:50%;background:#111;color:#fff;font-size:10px;text-align:center;line-height:18px}
.nav{left:578px;top:80px;display:flex;gap:0;font-size:14px;letter-spacing:.4px;color:#222}
.nav a{color:inherit;text-decoration:none}
.nav-about{left:578px;top:80px}
.nav-how{left:730px;top:80px}
.nav-contact{left:1032px;top:80px}

/* hero */
.hero{left:0;top:130px;width:1200px;height:586px;background:linear-gradient(135deg,#5b5e63 0%,#8d8b88 30%,#b9b5ad 55%,#7e7a74 80%,#4b4a48 100%)}
.hero-shade{left:0;top:130px;width:1200px;height:586px;background:rgba(0,0,0,.18)}
.hero-title{left:0;top:278px;width:1200px;text-align:center;font-family:"Montserrat",sans-serif;font-weight:700;font-size:57px;color:var(--white);letter-spacing:.5px}
.hero-sub{left:0;top:356px;width:1200px;text-align:center;font-size:15px;font-weight:700;color:var(--white)}
.hero-btn{left:515px;top:408px;width:125px;height:49px;background:var(--brand);color:var(--white);font-family:"Montserrat",sans-serif;font-weight:700;font-size:19px;text-align:center;line-height:49px;letter-spacing:.5px}
.hero-dots{left:556px;top:646px;display:flex;gap:9px}
.hero-dots span{width:15px;height:15px;border-radius:50%;background:var(--white)}
.hero-dots span.active{background:transparent;border:2px solid var(--white)}

/* sidebar */
.categories{left:98px;top:766px;width:235px;height:514px;border:1px solid var(--line);box-shadow:0 0 8px rgba(0,0,0,.08);background:var(--white)}
.categories h3{font-family:"Montserrat",sans-serif;font-size:15px;font-weight:700;padding:20px 0 0 20px;height:58px;border-bottom:1px solid var(--line);letter-spacing:.2px}
.categories ul{list-style:none;padding:22px 0 0 45px}
.categories li{font-size:13px;height:50.5px;color:#333}
.categories li::before{content:"»";margin-right:8px;font-weight:700}
.promo{left:98px;width:235px;box-shadow:0 0 8px rgba(0,0,0,.12)}
.promo-one{top:1367px;height:286px;background:linear-gradient(180deg,#f1ebe0 0%,#e9e0cf 55%,#d9c96a 75%,#c9b98e 100%)}
.promo-one-head{left:98px;top:1367px;width:235px;height:120px}
.promo-one-title{left:98px;top:1383px;width:235px;text-align:center;color:var(--white);font-size:26px;line-height:33px}
.promo-two{top:1685px;height:157px;background:linear-gradient(180deg,#f4f1ea 0%,#e6d7a0 45%,#5f9a9a 100%)}
.promo-two-title{left:98px;top:1706px;width:235px;text-align:center;font-size:20px;color:#555}
.promo-three{top:1877px;height:180px;background:linear-gradient(180deg,#8ec9c3 0%,#8bc2bc 60%,#8d8a86 80%,#b98c62 100%)}
.promo-three-title{left:98px;top:1906px;width:235px;text-align:center;font-size:27px;font-weight:700;color:var(--white)}

/* products */
.products-title{left:376px;top:784px;width:723px;text-align:center;font-family:"Montserrat",sans-serif;font-weight:800;font-size:35px;color:var(--brand);letter-spacing:.5px}
.arrow-btn{top:833px;width:24px;height:24px;border:1px solid #bbb;background:var(--white)}
.arrow-prev{left:1043px}.arrow-next{left:1073px}
.card{width:219px;height:370px;background:var(--white);box-shadow:0 0 14px rgba(0,0,0,.13)}
.card .photo{position:absolute;left:40px;top:18px;width:139px;height:150px;border-radius:6px}
.card .badge{position:absolute;left:10px;top:14px;background:#222;color:#fff;font-size:8px;padding:2px 7px;letter-spacing:.5px}
.card h4{position:absolute;left:0;top:188px;width:100%;text-align:center;font-family:"Montserrat",sans-serif;font-weight:600;font-size:16.5px;letter-spacing:.3px}
.card p{position:absolute;left:18px;top:230px;width:183px;text-align:center;font-size:11px;line-height:19px;color:var(--muted)}
.card .old{position:absolute;left:28px;top:308px;font-size:15px;color:#555;text-decoration:line-through}
.card .new{position:absolute;right:28px;top:306px;font-size:16px;font-weight:800;color:#111}
.col1{left:376px}.col2{left:629px}.col3{left:880px}
.row1{top:872px}.row2{top:1280px}.row3{top:1686px}

/* footer */
.footer{left:0;top:2131px;width:1200px;height:307px;background:var(--brand)}
.footer h5{position:absolute;font-weight:400;font-size:23px;color:var(--white)}
.footer-divider{top:2195px;width:1px;height:190px;background:rgba(255,255,255,.14)}
.f-link{font-size:16.5px;color:var(--footer-text);line-height:29px}
.contact-line{font-size:17px;color:var(--footer-text);line-height:26px}
.contact-strong{font-size:18px;color:var(--white)}
.newsletter{left:790px;top:2222px;width:312px;height:46px;background:var(--white);border:3px solid var(--white)}
.newsletter-input{left:802px;top:2236px;font-size:14px;color:#8a8a8a;letter-spacing:.3px}
.newsletter-btn{left:998px;top:2228px;width:99px;height:34px;background:var(--brand);color:var(--white);font-size:13px;font-weight:800;text-align:center;line-height:34px}
.footer-social{left:790px;top:2291px}

.bottom-bar{left:0;top:2438px;width:1200px;height:87px;background:var(--white)}
.copyright{left:98px;top:2473px;font-size:13px;color:#555}
.accept{left:864px;top:2473px;font-size:13px;color:#555}
.pay{top:2468px;height:24px;padding:0 6px;border:1px solid #ddd;font-size:10px;font-weight:700;color:var(--brand);line-height:22px;text-align:center}
</style>
</head>
<body>

<header>
  <div class="abs brand-name">novella</div>
  <div class="abs brand-tag">HOME GOODS</div>
  <div class="abs connect">Connect Us:</div>
  <div class="abs social header-social" aria-label="Social links"><span class="s1"></span><span class="s2"></span><span class="s3"></span><span class="s4"></span></div>
  <svg class="abs cart" width="22" height="22" viewBox="0 0 22 22" aria-label="Cart"><path d="M1 3h4l3 11h10l3-8H7" fill="none" stroke="#333" stroke-width="1.8"/><circle cx="9" cy="18" r="1.8" fill="#333"/><circle cx="17" cy="18" r="1.8" fill="#333"/></svg>
  <div class="abs cart-count">0</div>
  <nav>
    <a class="abs nav-about" style="font-size:14px;color:#222;text-decoration:none">ABOUT NOVELLA</a>
    <a class="abs nav-how" style="font-size:14px;color:#222;text-decoration:none">HOW DOES THIS CRAZINESS WORK?</a>
    <a class="abs nav-contact" style="font-size:14px;color:#222;text-decoration:none">CONTACT</a>
  </nav>
</header>

<section>
  <div class="abs hero" role="img" aria-label="Photo of a bed with colourful patterned throw pillows and a bedside lamp"></div>
  <div class="abs hero-shade"></div>
  <h1 class="abs hero-title">We will be Selling&nbsp; Home Goods</h1>
  <p class="abs hero-sub">Lorem ipsum dolor sit amet, consectetur adipiscing elit, sed do eiusmod tempor incididunt ut labore et dolore magna aliqua.</p>
  <div class="abs hero-btn">BUY NOW !</div>
  <div class="abs hero-dots"><span class="active"></span><span></span><span></span><span></span></div>
</section>

<aside>
  <div class="abs categories">
    <h3>PRODUCT CATEGORIES</h3>
    <ul>
      <li>Vases</li><li>Throw Pillows</li><li>Blankets and Throws</li><li>For Your Floors</li><li>For Your Walls</li><li>For Your Table</li><li>For Your Bedside</li><li>Let THere Be Light</li><li>Put Your Feet Up</li>
    </ul>
  </div>
  <div class="abs promo promo-one" role="img" aria-label="Photo of cream and yellow cushions on a sofa"></div>
  <svg class="abs promo-one-head" viewBox="0 0 235 120" preserveAspectRatio="none"><path d="M0 0H235V96Q117 150 0 96Z" fill="var(--brand)"/><path d="M0 96Q117 150 235 96" fill="none" stroke="#fff" stroke-width="3"/></svg>
  <div class="abs promo-one-title">Novella<br>Home Goods</div>
  <div class="abs promo promo-two" role="img" aria-label="Photo of teal vases with yellow flowers"></div>
  <div class="abs promo-two-title">Special Products</div>
  <div class="abs promo promo-three" role="img" aria-label="Photo of a grey sofa with cushions against a teal wall"></div>
  <div class="abs promo-three-title">Home Goods</div>
</aside>

<main>
  <h2 class="abs products-title">OUR PRODUCTS</h2>
  <svg class="abs arrow-btn arrow-prev" viewBox="0 0 24 24"><path d="M14 7l-5 5 5 5" fill="none" stroke="#555" stroke-width="1.5"/></svg>
  <svg class="abs arrow-btn arrow-next" viewBox="0 0 24 24"><path d="M10 7l5 5-5 5" fill="none" stroke="#555" stroke-width="1.5"/></svg>

  <article class="abs card col1 row1"><div class="photo" role="img" aria-label="Wicker picnic basket" style="background:radial-gradient(circle,#b98a52 0%,#e8d8c2 60%,#fff 80%)"></div><span class="badge">NEW</span><h4>FINIBUS BONORUM</h4><p>Sed ut perspiciatis unde omnis iste natus error sit volupta accusantium doloremque..</p><span class="old">$115.20</span><span class="new">$100.20</span></article>
  <article class="abs card col2 row1"><div class="photo" role="img" aria-label="Cocktail shaker set" style="background:radial-gradient(circle,#555 0%,#c9c9c9 55%,#fff 80%)"></div><h4>EIUSMOD TEMPOR</h4><p>Sed ut perspiciatis unde omnis iste natus error sit volupta accusantium doloremque..</p><span class="old">$175.20</span><span class="new">$150.20</span></article>
  <article class="abs card col3 row1"><div class="photo" role="img" aria-label="Coffee bag and mug" style="background:radial-gradient(circle,#6b4e36 0%,#d8ccbf 55%,#fff 80%)"></div><h4>MAGNA ALIQUA</h4><p>Sed ut perspiciatis unde omnis iste natus error sit volupta accusantium doloremque..</p><span class="old">$250.20</span><span class="new">$175.20</span></article>

  <article class="abs card col1 row2"><div class="photo" role="img" aria-label="White bar stool" style="background:radial-gradient(circle,#bdbdbd 0%,#eee 55%,#fff 80%)"></div><h4>PERSPICIATIS UNDE</h4><p>Sed ut perspiciatis unde omnis iste natus error sit volupta accusantium doloremque..</p><span class="old">$150.20</span><span class="new">$120.20</span></article>
  <article class="abs card col2 row2"><div class="photo" role="img" aria-label="Gift box and candles" style="background:radial-gradient(circle,#f07a7a 0%,#f2e0c8 55%,#fff 80%)"></div><h4>OMNIS ISTE NATUS</h4><p>Sed ut perspiciatis unde omnis iste natus error sit volupta accusantium doloremque..</p><span class="old">$175.20</span><span class="new">$160.20</span></article>
  <article class="abs card col3 row2"><div class="photo" role="img" aria-label="Glass teacup on a decorated plate" style="background:radial-gradient(circle,#d7b98a 0%,#efe6d8 55%,#fff 80%)"></div><span class="badge">NEW</span><h4>VOLUPTATEM QUIA</h4><p>Sed ut perspiciatis unde omnis iste natus error sit volupta accusantium doloremque..</p><span class="old">$200.20</span><span class="new">$175.20</span></article>

  <article class="abs card col1 row3"><div class="photo" role="img" aria-label="Baby bottles" style="background:radial-gradient(circle,#f0b14a 0%,#f4ece0 55%,#fff 80%)"></div><h4>NUMQUAM EIUS</h4><p>Sed ut perspiciatis unde omnis iste natus error sit volupta accusantium doloremque..</p><span class="old">$225.20</span><span class="new">$170.20</span></article>
  <article class="abs card col2 row3"><div class="photo" role="img" aria-label="Ornate decorative vases" style="background:radial-gradient(circle,#8a6a2e 0%,#e4d7c0 55%,#fff 80%)"></div><h4>MODI TEMPORA</h4><p>Sed ut perspiciatis unde omnis iste natus error sit volupta accusantium doloremque..</p><span class="old">$175.20</span><span class="new">$150.20</span></article>
  <article class="abs card col3 row3"><div class="photo" role="img" aria-label="Wooden shelf and bench" style="background:radial-gradient(circle,#b98d5c 0%,#efe3d3 55%,#fff 80%)"></div><h4>ALIQUAM QUAERAT</h4><p>Sed ut perspiciatis unde omnis iste natus error sit volupta accusantium doloremque..</p><span class="old">$230.20</span><span class="new">$185.20</span></article>
</main>

<footer>
  <div class="abs footer">
    <h5 style="left:98px;top:49px">Quick Links</h5>
    <h5 style="left:478px;top:49px;font-size:21px">Contact Us</h5>
    <h5 style="left:790px;top:49px">Join Newsletters</h5>
  </div>
  <div class="abs footer-divider" style="left:420px"></div>
  <div class="abs footer-divider" style="left:748px"></div>
  <div class="abs f-link" style="left:98px;top:2234px">Policies<br>Orders<br>Return<br>Bulk Discount</div>
  <div class="abs f-link" style="left:286px;top:2234px">Quality<br>Privacy<br>Terms of Use</div>
  <div class="abs contact-line" style="left:478px;top:2226px">Novella , Street Name, City<br>Address, Country, Pin Code.</div>
  <svg class="abs" style="left:480px;top:2290px" width="16" height="16" viewBox="0 0 16 16"><path d="M3 1l3 3-2 2c1 2 3 4 5 5l2-2 3 3-2 3C7 15 1 9 1 3z" fill="#fff"/></svg>
  <div class="abs contact-strong" style="left:508px;top:2286px">+1-234-567-8900</div>
  <svg class="abs" style="left:480px;top:2320px" width="16" height="12" viewBox="0 0 16 12"><rect width="16" height="12" fill="#fff"/><path d="M0 0l8 6 8-6" fill="none" stroke="var(--brand)" stroke-width="1.5"/></svg>
  <div class="abs contact-strong" style="left:508px;top:2314px">info@companyname.com</div>
  <div class="abs newsletter"></div>
  <div class="abs newsletter-input">EMAIL ADDRESS</div>
  <div class="abs newsletter-btn">SUBSCRIBE</div>
  <div class="abs social footer-social"><span class="s1"></span><span class="s2"></span><span class="s3"></span><span class="s4"></span></div>

  <div class="abs bottom-bar"></div>
  <div class="abs copyright">© 2017 Novella Home Goods.&nbsp; All right reserved.&nbsp; Term of Use</div>
  <div class="abs accept">We Accept:</div>
  <div class="abs pay" style="left:940px">Cardova</div>
  <div class="abs pay" style="left:1000px">Meridian</div>
  <div class="abs pay" style="left:1064px">Amplex</div>
  <div class="abs pay" style="left:1120px">Monvex</div>
</footer>

</body>
</html>
```